Timber Crest Construction Needs business card

Hey we are in need of business card designs. I have upload our logo as a guideline, but free feel to run with it or come up with something unique.
Pls have fun with it and be creative. the name says it all!
i will give some directions after i see a few entries..
Updates
Logo source file has been uploaded..
Hey because of the logo is so colourful already.
Can we have a few submissions with less colour.
Also we are looking for clever/hidden/descriptive business card.

```html
<!DOCTYPE html>
<html lang="en">
<head>
<meta charset="utf-8">
<title>Timber Crest Construction – Business Card</title>
<link rel="stylesheet" href="https://fonts.googleapis.com/css2?family=Arimo:wght@400;700&display=swap">
<style>
  :root {
    --stage: #ecebe8;
    --card: #ffffff;
    --ink: #1c1c1c;
    --brand-grey: #5b5f61;
    --accent-blue: #2c6fa6;
    --rule: #dfe6ee;
    --shadow: 0 6px 18px rgba(0,0,0,0.18);
  }
  * { box-sizing: border-box; margin: 0; padding: 0; }
  html, body {
    width: 1200px;
    height: 470px;
    overflow: hidden;
    background: var(--stage);
    font-family: "Arimo", Arial, sans-serif;
  }
  .stage {
    position: relative;
    width: 1200px;
    height: 470px;
  }
  .card {
    position: absolute;
    top: 85px;
    width: 520px;
    height: 300px;
    background: var(--card);
    box-shadow: var(--shadow);
  }
  .card--front { left: 45px; }
  .card--back  { left: 635px; }

  /* front */
  .holder {
    position: absolute;
    top: 26px;
    right: 30px;
    text-align: right;
    color: var(--accent-blue);
  }
  .holder__name  { font-size: 18px; letter-spacing: 0.3px; }
  .holder__title { font-size: 13px; margin-top: 1px; }

  .brand {
    position: absolute;
    color: var(--brand-grey);
    font-weight: 700;
    text-transform: uppercase;
    line-height: 1;
  }
  .brand__square {
    display: inline-block;
    background: var(--brand-grey);
    vertical-align: middle;
  }
  .card--front .brand { left: 30px; top: 72px; }
  .card--front .brand__line1 { font-size: 30px; letter-spacing: -0.5px; }
  .card--front .brand__line2 { font-size: 30px; letter-spacing: -0.5px; margin-top: 4px; }
  .card--front .brand__square { width: 14px; height: 14px; margin-left: 8px; }

  .contact {
    position: absolute;
    left: 30px;
    bottom: 26px;
    list-style: none;
    color: var(--ink);
    font-size: 13px;
    line-height: 21px;
  }
  .contact li { display: flex; align-items: center; gap: 6px; }
  .contact svg { width: 12px; height: 12px; flex: none; fill: var(--ink); }
  .contact__address { margin-top: 5px; font-size: 13.5px; }

  .base-rule {
    position: absolute;
    left: 0; right: 0;
    height: 3px;
    background: var(--rule);
  }

  /* back */
  .card--back .brand { left: 110px; top: 82px; }
  .card--back .brand__line1 { font-size: 40px; letter-spacing: -0.5px; }
  .card--back .brand__line2 { font-size: 40px; letter-spacing: -0.5px; margin-top: 4px; }
  .card--back .brand__square { width: 18px; height: 18px; margin-left: 10px; }
  .website {
    position: absolute;
    left: 110px;
    top: 182px;
    font-size: 19px;
    color: var(--ink);
    letter-spacing: 0.3px;
  }
  .card--back .base-rule { bottom: 22px; left: 30px; right: 30px; }
</style>
</head>
<body>
<main class="stage">

  <section class="card card--front" aria-label="Card front">
    <div class="holder">
      <div class="holder__name">Your Name</div>
      <div class="holder__title">Title</div>
    </div>

    <div class="brand">
      <div class="brand__line1">Timber Crest<span class="brand__square"></span></div>
      <div class="brand__line2">Construction</div>
    </div>

    <ul class="contact">
      <li>
        <svg viewBox="0 0 24 24" aria-hidden="true"><path d="M6.6 10.8a15 15 0 0 0 6.6 6.6l2.2-2.2a1 1 0 0 1 1-.25 11.4 11.4 0 0 0 3.6.57 1 1 0 0 1 1 1V20a1 1 0 0 1-1 1A17 17 0 0 1 3 4a1 1 0 0 1 1-1h3.5a1 1 0 0 1 1 1c0 1.25.2 2.45.57 3.6a1 1 0 0 1-.25 1z"/></svg>
        0400 135 792
      </li>
      <li>
        <svg viewBox="0 0 24 24" aria-hidden="true"><path d="M6.6 10.8a15 15 0 0 0 6.6 6.6l2.2-2.2a1 1 0 0 1 1-.25 11.4 11.4 0 0 0 3.6.57 1 1 0 0 1 1 1V20a1 1 0 0 1-1 1A17 17 0 0 1 3 4a1 1 0 0 1 1-1h3.5a1 1 0 0 1 1 1c0 1.25.2 2.45.57 3.6a1 1 0 0 1-.25 1z"/></svg>
        0400 135 792
      </li>
      <li>
        <svg viewBox="0 0 24 24" aria-hidden="true"><path d="M2 6h20v12H2z" fill="none" stroke="#1c1c1c" stroke-width="2.4"/><path d="M2 6l10 7 10-7" fill="none" stroke="#1c1c1c" stroke-width="2.4"/></svg>
        hello@timbercrestbuild.com
      </li>
      <li>
        <svg viewBox="0 0 24 24" aria-hidden="true"><circle cx="12" cy="12" r="9.5" fill="none" stroke="#1c1c1c" stroke-width="2.4"/><path d="M2.5 12h19M12 2.5c-3.5 4-3.5 15 0 19M12 2.5c3.5 4 3.5 15 0 19" fill="none" stroke="#1c1c1c" stroke-width="1.8"/></svg>
        www.timbercrestbuild.com
      </li>
      <li class="contact__address">Street Name City Name, State Zipcode</li>
    </ul>
  </section>

  <section class="card card--back" aria-label="Card back">
    <div class="brand">
      <div class="brand__line1">Timber Crest<span class="brand__square"></span></div>
      <div class="brand__line2">Construction</div>
    </div>
    <div class="website">www.timbercrestbuild.com</div>
    <div class="base-rule"></div>
  </section>

</main>
</body>
</html>
```